Birchline Septic Solutions

Would like to see some single sided ones but would also like to see some double sided with one sided only being the logo. Owners name is Colin Vandro. Phone number is 555-214-0387
Services are pumping, inspections, installs, and repairs

Contact Information for Business Card

555-241-0387 Colin Vandro Maplebrook, OH

```html
<!DOCTYPE html>
<html lang="en">
<head>
<meta charset="utf-8">
<title>Birchline Septic Solutions – Business Cards</title>
<link rel="stylesheet" href="https://fonts.googleapis.com/css2?family=Montserrat:wght@500;600;800&display=swap">
<style>
  :root {
    --bg: #c9c9c9;
    --card: #111111;
    --card-edge: #2bbfba;
    --teal: #2bbfba;
    --white: #ffffff;
    --divider: #3a3a3a;
    --pattern-dark: #0c0c0c;
    --pattern-light: #1e1e1e;
  }
  * { box-sizing: border-box; margin: 0; padding: 0; }
  html, body { width: 1200px; height: 800px; overflow: hidden; }
  body {
    background: var(--bg);
    font-family: "Montserrat", Arial, sans-serif;
    display: flex;
    align-items: center;
    justify-content: center;
    gap: 40px;
  }
  .card {
    position: relative;
    width: 520px;
    height: 297px;
    background: var(--card);
    border-bottom: 3px solid var(--card-edge);
    box-shadow: 0 14px 30px rgba(0,0,0,.3);
    overflow: hidden;
  }
  /* front */
  .card-front .brand {
    position: absolute;
    left: 40px;
    top: 70px;
    width: 200px;
    color: var(--white);
    font-weight: 800;
    font-size: 26px;
    line-height: 1.15;
    text-transform: uppercase;
    letter-spacing: .5px;
  }
  .card-front .divider {
    position: absolute;
    left: 262px;
    top: 60px;
    width: 1px;
    height: 120px;
    background: var(--divider);
  }
  .contact {
    position: absolute;
    left: 286px;
    top: 78px;
    color: var(--white);
  }
  .contact .owner {
    color: var(--teal);
    font-weight: 800;
    font-size: 22px;
    text-transform: uppercase;
    margin-bottom: 14px;
  }
  .contact .line {
    display: flex;
    align-items: center;
    gap: 8px;
    font-weight: 500;
    font-size: 15px;
    margin-bottom: 6px;
  }
  .contact svg { width: 20px; height: 20px; flex: none; }
  .service-band {
    position: absolute;
    left: 0; right: 0; bottom: 0;
    height: 50px;
    background: var(--teal);
    color: var(--white);
    font-weight: 600;
    font-size: 15px;
    letter-spacing: 1px;
    display: flex;
    align-items: center;
    justify-content: center;
    text-transform: uppercase;
  }
  .service-band .dot { margin: 0 8px; }
  /* back */
  .card-back .pattern {
    position: absolute;
    inset: 0;
    background: linear-gradient(135deg, var(--pattern-dark), var(--pattern-light) 55%, var(--pattern-dark));
  }
  .card-back .brand-mark {
    position: absolute;
    right: 70px;
    bottom: 70px;
    color: var(--white);
    font-weight: 800;
    font-size: 26px;
    text-transform: uppercase;
  }
</style>
</head>
<body>
  <section class="card card-front" aria-label="Business card front">
    <div class="brand">Birchline Septic Solutions</div>
    <div class="divider"></div>
    <div class="contact">
      <div class="owner">Colin Vandro</div>
      <div class="line">
        <svg viewBox="0 0 20 20" aria-hidden="true"><circle cx="10" cy="10" r="10" fill="var(--teal)"/><path d="M7 5.5l1.8 2.2-1 1.2a7 7 0 003.3 3.3l1.2-1 2.2 1.8-1 1.5c-3.8.3-8-3.9-7.7-7.7z" fill="var(--card)"/></svg>
        <span>555-214-0387</span>
      </div>
      <div class="line">
        <svg viewBox="0 0 20 20" aria-hidden="true"><circle cx="10" cy="10" r="10" fill="var(--teal)"/><path d="M10 4.5a3.5 3.5 0 00-3.5 3.5c0 2.6 3.5 7 3.5 7s3.5-4.4 3.5-7A3.5 3.5 0 0010 4.5z" fill="var(--card)"/><circle cx="10" cy="8" r="1.3" fill="var(--teal)"/></svg>
        <span>Maplebrook, OH</span>
      </div>
    </div>
    <div class="service-band">
      Pumping<span class="dot">•</span>Inspections<span class="dot">•</span>Installs<span class="dot">•</span>Repairs
    </div>
  </section>

  <section class="card card-back" aria-label="Business card back">
    <div class="pattern" role="img" aria-label="Tone-on-tone repeating brand emblem pattern"></div>
    <div class="brand-mark">Birchline</div>
  </section>
</body>
</html>
```